Reach Crafters Unique Marketing Website Design

I am starting a new company that is a thought leader in the marketing consulting space. The company is called Reach Crafters. We intend to build a Wordpress site on the Astra Theme with the Spectra builder. Our goal is to become the leading voice that empowers high-ticket service business leaders to become Reach Crafters by equipping them with the cutting-edge frameworks and decision grade intelligence taught in leading business schools. What we are looking for is a website design that is clean and professional, making some use of white space well also being eye catching and distinctive in the consulting space. We will probably want to have a video on the homepage not in the hero section, but just below to explain the company and what we do. Our tagline is "Be found. Be chosen." I have attached a brand guide with some messaging, our typography choices, and our color system. The full site will have a primary nav that is four pages - About us, Services, Insights (essentially a blog), and Contact Us. The goal of this project is to develop an art direction that I can give to a designer to build loads of new pages.

Target Market(s)

Business owners (mostly male) from 30-60 years old, looking to fix their sales and marketing funnel.

Industry/Entity Type

Marketing consulting

Font styles to use
Sans Serif

Requirements
Must have
• A clean, professional design that builds trust with owners of high-ticket service businesses. We need a space for explainer video, and sections that tell prospects what we do. Would also like to have a blog carousel.
Nice to have
• Social feeds, if possible. See attached documents for colors and fonts.
Should not have
• Our feel is professional enough to be trustworthy, but unique enough to be memorable. Cartoon ideas do not meet the professional test, and we do not want the website to appear feminine.

```html
<!DOCTYPE html>
<html lang="en">
<head>
<meta charset="utf-8">
<title>Reach Crafters — Marketing Consulting</title>
<link href="https://fonts.googleapis.com/css2?family=Oswald:wght@300;400;500;600&family=Inter:ital,wght@0,400;0,500;0,600;0,700;1,400;1,500&display=swap" rel="stylesheet">
<style>
:root{
  --blue:#2d5cf2;
  --navy:#0c1a32;
  --footer:#0e1a2f;
  --ink:#1d2230;
  --text:#5b6170;
  --light:#f6f6f7;
  --white:#ffffff;
  --star:#f28a1e;
  --head:'Oswald',sans-serif;
  --body:'Inter',sans-serif;
}
*{margin:0;padding:0;box-sizing:border-box}
html,body{width:1200px;height:4850px;overflow:hidden}
body{font-family:var(--body);color:var(--ink);background:var(--white);position:relative}
section,header,footer{position:absolute;left:0;width:1200px}
.abs{position:absolute}
.hl{color:var(--blue)}
.sec-title{position:absolute;left:0;width:1200px;text-align:center;font-family:var(--head);font-weight:500;font-size:37px;color:var(--ink)}
.sec-rule{position:absolute;left:578px;width:44px;height:2px;background:var(--blue)}
.sec-sub{position:absolute;left:0;width:1200px;text-align:center;font-size:13.5px;color:var(--text);line-height:22px}
.btn{position:absolute;display:flex;align-items:center;justify-content:center;gap:6px;background:var(--blue);color:#fff;font-size:13px;font-weight:500;border-radius:2px}
.btn svg{width:14px;height:10px}

/* header */
.site-header{top:0;height:78px;background:#fff;border-bottom:1px solid #e8e8ea}
.brand{position:absolute;left:70px;top:24px;display:flex;align-items:center;gap:10px}
.brand-mark{width:14px;height:14px;background:var(--blue)}
.brand-name{font-size:24px;font-weight:600;color:var(--ink)}
.nav{position:absolute;right:72px;top:22px;display:flex;align-items:center}
.nav a{font-size:12px;color:var(--text);text-decoration:none;margin-right:54px}
.nav .btn{position:static;width:98px;height:34px;font-size:12px}

/* hero */
.hero{top:78px;height:543px}
.hero-photo{position:absolute;inset:0;background:linear-gradient(90deg,#1b1d22 0%,#2b2824 40%,#6f6253 65%,#a99882 100%)}
.hero-shade{position:absolute;inset:0;background:linear-gradient(90deg,rgba(10,12,18,.82) 0%,rgba(10,12,18,.55) 45%,rgba(10,12,18,0) 75%)}
.hero-tag{left:72px;top:122px;font-size:18px;font-style:italic;color:#fff}
.hero-title{left:72px;top:160px;font-family:var(--head);color:#fff;font-size:41px;line-height:56px}
.hero-title b{font-weight:600}
.hero-title b u{text-decoration:none;border-bottom:4px solid var(--blue)}
.hero-title span{font-weight:300;display:block}
.hero-text{left:72px;top:278px;width:400px;font-size:13.5px;line-height:22px;color:#eee}
.hero .btn{left:72px;top:375px;width:134px;height:40px}

/* empowering */
.empower{top:621px;height:555px;background:var(--light)}
.feature{position:absolute;top:192px;width:284px;height:285px;background:#fff;padding:28px 28px}
.feature svg{width:62px;height:62px}
.feature h3{font-size:16px;font-weight:600;margin-top:20px}
.feature .rule{width:30px;height:2px;background:var(--blue);margin:12px 0 14px}
.feature p{font-size:12.3px;line-height:19px;color:var(--text)}

/* video */
.video{top:1176px;height:815px;background:#fff}
.video-frame{position:absolute;left:140px;top:216px;width:919px;height:518px;background:#fff;padding:9px;box-shadow:0 3px 14px rgba(0,0,0,.14)}
.video-still{width:100%;height:100%;background:linear-gradient(135deg,#4a4540 0%,#8b7a68 40%,#6e6a6a 70%,#3c3a3e 100%);position:relative}
.play{position:absolute;left:430px;top:230px;width:60px;height:60px;border-radius:50%;background:var(--blue);border:4px solid #fff;display:flex;align-items:center;justify-content:center}

/* stats */
.stats{top:1991px;height:396px;background:var(--navy)}
.stat{position:absolute;top:80px;width:200px;text-align:center}
.stat svg{width:196px;height:196px}
.stat .num{position:absolute;left:0;top:68px;width:196px;text-align:center;font-family:var(--head);font-size:41px;font-weight:500;color:#fff}
.stat .label{margin-top:22px;font-size:14px;color:#fff}

/* about */
.about{top:2387px;height:563px;background:#fff}
.about-photo{position:absolute;left:140px;top:76px;width:419px;height:410px;background:linear-gradient(90deg,#dfe6ee 0%,#cfd8e2 49%,#fff 49.6%,#fff 50.4%,#e5e5e5 51%,#cfcfcf 100%)}
.about-title{left:624px;top:114px;font-family:var(--head);font-size:38px;font-weight:500;color:var(--ink)}
.about-lead{left:624px;top:190px;font-size:14.5px;font-weight:600}
.about-text{left:624px;width:432px;font-size:12.5px;line-height:20.5px;color:var(--text)}
.about .btn{left:624px;top:397px;width:134px;height:40px}

/* testimonials */
.testi{top:2950px;height:565px;background:var(--light)}
.quote{position:absolute;top:192px;width:284px;height:253px;background:#fff;padding:28px 26px}
.stars{display:flex;gap:3px}
.stars svg{width:14px;height:14px}
.qmark{position:absolute;right:26px;top:22px;font-family:Georgia,serif;font-size:60px;line-height:60px;color:#b9c6f6}
.quote p{margin-top:14px;font-size:12px;line-height:23px;font-style:italic;color:var(--text)}
.author{position:absolute;left:26px;bottom:30px;display:flex;align-items:center;gap:10px}
.avatar{width:32px;height:32px;border-radius:50%;background:var(--blue);color:#fff;font-weight:700;font-size:14px;display:flex;align-items:center;justify-content:center}
.author b{font-size:14px;font-weight:600;display:block}
.author small{font-size:10px;color:var(--text)}
.dots{position:absolute;top:484px;left:561px;display:flex;gap:6px}
.dots i{width:7px;height:7px;border-radius:50%;background:#c7ccd6}
.dots i:first-child{background:var(--blue)}

/* blog */
.blog{top:3515px;height:659px;background:#fff}
.post{position:absolute;top:151px;width:284px}
.post-img{height:152px;position:relative}
.date{position:absolute;right:4px;top:0;width:34px;height:44px;background:var(--blue);color:#fff;text-align:center;font-weight:700;font-size:18px;line-height:24px}
.date small{display:block;font-size:9px;font-weight:500;line-height:10px}
.post-body{margin:0 10px;background:#fff;box-shadow:0 3px 12px rgba(0,0,0,.09);padding:20px 22px 20px;height:190px}
.post-body h3{font-size:14.5px;font-weight:600;line-height:20px}
.post-body p{margin-top:10px;font-size:12px;line-height:20px;color:var(--text)}
.more{margin-top:8px;display:flex;align-items:center;gap:6px;font-size:12px;color:var(--blue);font-weight:500}
.more svg{width:14px;height:10px}

/* cta */
.cta{top:4174px;height:321px;background:var(--blue)}
.cta-title{top:72px;left:0;width:1200px;text-align:center;font-family:var(--head);font-size:39px;font-weight:300;color:#fff}
.cta-title b{font-weight:600}
.cta-text{top:132px;left:0;width:1200px;text-align:center;font-size:13.5px;line-height:23px;color:#fff}
.cta-btn{position:absolute;left:457px;top:213px;width:286px;height:41px;background:#fff;color:var(--blue);display:flex;align-items:center;justify-content:center;gap:8px;font-size:13px;font-weight:500}
.cta-btn svg{width:16px;height:10px}

/* footer */
.site-footer{top:4495px;height:355px;background:var(--footer);color:#fff}
.f-brand{left:140px;top:74px;font-size:19px;font-weight:600}
.f-about{left:140px;top:126px;width:240px;font-size:11.5px;line-height:19px;color:#dde1e8}
.follow{left:140px;top:197px;display:flex;align-items:center;gap:8px;font-size:11.5px}
.follow i{width:26px;height:26px;border-radius:50%;border:1px solid #52607a;display:block}
.follow i.on{background:var(--blue);border-color:var(--blue)}
.f-col h4{font-size:14px;font-weight:600}
.f-col .rule{width:110px;height:1px;background:#3c4a63;margin:10px 0 0;position:relative}
.f-col .rule::before{content:"";position:absolute;left:0;top:-1px;width:24px;height:3px;background:var(--blue)}
.f-col ul{list-style:none;margin-top:16px}
.f-col li{font-size:11.5px;color:#dde1e8;line-height:29px}
.contact-row{display:flex;align-items:flex-start;gap:16px;margin-top:16px;font-size:11.5px;line-height:21px;color:#dde1e8}
.c-ico{width:30px;height:30px;border-radius:50%;background:#fff;flex:none;display:flex;align-items:center;justify-content:center}
.c-ico.blue{background:var(--blue)}
.c-ico svg{width:15px;height:15px}
.copy{left:0;top:313px;width:1200px;text-align:center;font-size:10.5px;color:#c9ced8}
.copy-rule{left:0;top:296px;width:1200px;height:1px;background:#1f2b42}
</style>
</head>
<body>

<header class="site-header">
  <div class="brand"><span class="brand-mark"></span><span class="brand-name">Reach Crafters</span></div>
  <nav class="nav">
    <a>About Us</a><a>Services</a><a>Insights</a>
    <span class="btn">Contact Us</span>
  </nav>
</header>

<section class="hero">
  <div class="hero-photo" role="img" aria-label="Photo of a consulting team collaborating around a laptop in a modern office"></div>
  <div class="hero-shade"></div>
  <div class="abs hero-tag">Be Found. Be Chosen.</div>
  <h1 class="abs hero-title"><b>Empowering <u>High-Ticket</u></b><span>Service Business Leaders</span></h1>
  <p class="abs hero-text">Become a Reach Crafter with cutting-edge frameworks and decision-grade intelligence taught in leading business schools. Transform your sales and marketing funnel.</p>
  <span class="btn">Contact Us <svg viewBox="0 0 14 10"><path d="M0 5h12M8 1l4 4-4 4" stroke="#fff" fill="none" stroke-width="1.3"/></svg></span>
</section>

<section class="empower">
  <h2 class="sec-title" style="top:62px"><span class="hl">Empowering</span> Business Leaders Like You</h2>
  <div class="sec-rule" style="top:122px"></div>
  <p class="sec-sub" style="top:143px">We provide the tools, frameworks, and intelligence you need to dominate your market.</p>

  <div class="feature" style="left:140px">
    <svg viewBox="0 0 62 62" fill="none" stroke="#2d5cf2" stroke-width="2"><circle cx="31" cy="31" r="20"/><circle cx="31" cy="31" r="11"/><circle cx="31" cy="31" r="5"/><path d="M31 5v6M31 51v6M5 31h6M51 31h6M12.6 12.6l4.3 4.3M45.1 45.1l4.3 4.3M12.6 49.4l4.3-4.3M45.1 16.9l4.3-4.3"/></svg>
    <h3>Cutting-Edge Frameworks</h3><div class="rule"></div>
    <p>Learn the same advanced marketing strategies taught at top business schools, tailored for high-ticket service businesses. Implement proven systems that drive consistent results.</p>
  </div>
  <div class="feature" style="left:458px">
    <svg viewBox="0 0 62 62" fill="none" stroke="#2d5cf2" stroke-width="2"><circle cx="31" cy="18" r="12"/><path d="M27 14a4 4 0 1 1 5 4v3M31 24v1"/><path d="M31 30v14M31 44l-12-8h-6M31 44l12-8h6M31 44v12"/><circle cx="10" cy="36" r="3"/><circle cx="52" cy="36" r="3"/></svg>
    <h3>Decision-Grade Intelligence</h3><div class="rule"></div>
    <p>Get data-driven insights to fix leaks in your sales and marketing funnel—fast. We turn complex data into actionable strategies that boost your bottom line.</p>
  </div>
  <div class="feature" style="left:776px">
    <svg viewBox="0 0 62 62" fill="none" stroke="#2d5cf2" stroke-width="2"><path d="M14 6h24l10 10v24M14 6v48h22"/><path d="M38 6v10h10M20 22h18M20 30h18M20 38h12"/><circle cx="46" cy="48" r="9"/><path d="M42 48l3 3 5-6"/></svg>
    <h3>Proven Results</h3><div class="rule"></div>
    <p>Become the obvious choice for your ideal clients with positioning that commands premium fees. Join leaders who have transformed their businesses with our guidance.</p>
  </div>
</section>

<section class="video">
  <h2 class="sec-title" style="top:60px">Discover How We <span class="hl">Transform</span> Marketing Funnels</h2>
  <div class="sec-rule" style="top:120px"></div>
  <p class="sec-sub" style="top:141px">Learn how our proven frameworks help high-ticket service businesses attract premium clients<br>and increase conversion rates.</p>
  <div class="video-frame">
    <div class="video-still" role="img" aria-label="Explainer video still showing a large group of business professionals">
      <div class="play"><svg width="20" height="22" viewBox="0 0 20 22"><path d="M3 2l15 9-15 9z" fill="#fff"/></svg></div>
    </div>
  </div>
</section>

<section class="stats">
  <div class="stat" style="left:148px">
    <svg viewBox="0 0 196 196"><circle cx="98" cy="98" r="72" fill="none" stroke="#23396d" stroke-width="48"/><circle cx="98" cy="98" r="72" fill="none" stroke="#2d5cf2" stroke-width="48" stroke-dasharray="248 453" transform="rotate(-90 98 98)"/><circle cx="98" cy="98" r="48" fill="#0c1a32"/></svg>
    <div class="num">170+</div><div class="label">Clients Served</div>
  </div>
  <div class="stat" style="left:384px">
    <svg viewBox="0 0 196 196"><circle cx="98" cy="98" r="72" fill="none" stroke="#23396d" stroke-width="48"/><circle cx="98" cy="98" r="72" fill="none" stroke="#2d5cf2" stroke-width="48" stroke-dasharray="240 453" transform="rotate(-90 98 98)"/><circle cx="98" cy="98" r="48" fill="#0c1a32"/></svg>
    <div class="num">53M+</div><div class="label">Revenue Generated</div>
  </div>
  <div class="stat" style="left:620px">
    <svg viewBox="0 0 196 196"><circle cx="98" cy="98" r="72" fill="none" stroke="#23396d" stroke-width="48"/><circle cx="98" cy="98" r="72" fill="none" stroke="#2d5cf2" stroke-width="48" stroke-dasharray="190 453" transform="rotate(-90 98 98)"/><circle cx="98" cy="98" r="48" fill="#0c1a32"/></svg>
    <div class="num">3.2x</div><div class="label">Avg. ROI Increase</div>
  </div>
  <div class="stat" style="left:855px">
    <svg viewBox="0 0 196 196"><circle cx="98" cy="98" r="72" fill="none" stroke="#23396d" stroke-width="48"/><circle cx="98" cy="98" r="72" fill="none" stroke="#2d5cf2" stroke-width="48" stroke-dasharray="210 453" transform="rotate(-90 98 98)"/><circle cx="98" cy="98" r="48" fill="#0c1a32"/></svg>
    <div class="num">92%</div><div class="label">Client Retention</div>
  </div>
</section>

<section class="about">
  <div class="about-photo" role="img" aria-label="Split photo of a consultant in a suit writing notes at a desk"></div>
  <h2 class="abs about-title">About Reach Crafters</h2>
  <div class="abs about-lead">Empowering Business Leaders to Master Demand.</div>
  <p class="abs about-text" style="top:220px">At Reach Crafters, we believe every high-ticket service business deserves access to the same strategic frameworks used by Apex 500 companies.</p>
  <p class="abs about-text" style="top:291px">Our team brings together decades of experience in marketing strategy, sales optimization, and business development. We've distilled the best practices from leading business schools and real-world success stories into actionable systems that drive results.</p>
  <span class="btn">Learn More <svg viewBox="0 0 14 10"><path d="M0 5h12M8 1l4 4-4 4" stroke="#fff" fill="none" stroke-width="1.3"/></svg></span>
</section>

<section class="testi">
  <h2 class="sec-title" style="top:64px">What Our <span class="hl">Happy Clients</span> Say About Us</h2>
  <div class="sec-rule" style="top:124px"></div>
  <p class="sec-sub" style="top:144px">We provide the tools, frameworks, and intelligence you need to dominate your market.</p>

  <div class="quote" style="left:140px">
    <div class="stars"><svg viewBox="0 0 14 14"><path d="M7 1l1.8 3.9 4.2.4-3.2 2.8 1 4.1L7 10 3.2 12.2l1-4.1L1 5.3l4.2-.4z" fill="#f28a1e"/></svg><svg viewBox="0 0 14 14"><path d="M7 1l1.8 3.9 4.2.4-3.2 2.8 1 4.1L7 10 3.2 12.2l1-4.1L1 5.3l4.2-.4z" fill="#f28a1e"/></svg><svg viewBox="0 0 14 14"><path d="M7 1l1.8 3.9 4.2.4-3.2 2.8 1 4.1L7 10 3.2 12.2l1-4.1L1 5.3l4.2-.4z" fill="#f28a1e"/></svg><svg viewBox="0 0 14 14"><path d="M7 1l1.8 3.9 4.2.4-3.2 2.8 1 4.1L7 10 3.2 12.2l1-4.1L1 5.3l4.2-.4z" fill="#f28a1e"/></svg><svg viewBox="0 0 14 14"><path d="M7 1l1.8 3.9 4.2.4-3.2 2.8 1 4.1L7 10 3.2 12.2l1-4.1L1 5.3l4.2-.4z" fill="#f28a1e"/></svg></div>
    <span class="qmark">”</span>
    <p>"Reach Crafters helped us identify critical leaks in our funnel that we had overlooked for years. Our lead quality improved by 300% in just 90 days."</p>
    <div class="author"><span class="avatar">A</span><div><b>Arlen Voss</b><small>CEO, Summit Advisory Group</small></div></div>
  </div>
  <div class="quote" style="left:458px">
    <div class="stars"><svg viewBox="0 0 14 14"><path d="M7 1l1.8 3.9 4.2.4-3.2 2.8 1 4.1L7 10 3.2 12.2l1-4.1L1 5.3l4.2-.4z" fill="#f28a1e"/></svg><svg viewBox="0 0 14 14"><path d="M7 1l1.8 3.9 4.2.4-3.2 2.8 1 4.1L7 10 3.2 12.2l1-4.1L1 5.3l4.2-.4z" fill="#f28a1e"/></svg><svg viewBox="0 0 14 14"><path d="M7 1l1.8 3.9 4.2.4-3.2 2.8 1 4.1L7 10 3.2 12.2l1-4.1L1 5.3l4.2-.4z" fill="#f28a1e"/></svg><svg viewBox="0 0 14 14"><path d="M7 1l1.8 3.9 4.2.4-3.2 2.8 1 4.1L7 10 3.2 12.2l1-4.1L1 5.3l4.2-.4z" fill="#f28a1e"/></svg><svg viewBox="0 0 14 14"><path d="M7 1l1.8 3.9 4.2.4-3.2 2.8 1 4.1L7 10 3.2 12.2l1-4.1L1 5.3l4.2-.4z" fill="#f28a1e"/></svg></div>
    <span class="qmark">”</span>
    <p>"The frameworks provided by Reach Crafters transformed how we approach client acquisition. We've increased our average deal size by 45% while reducing acquisition costs."</p>
    <div class="author"><span class="avatar">D</span><div><b>Daniel Okafor</b><small>Founder, Northline Partners</small></div></div>
  </div>
  <div class="quote" style="left:776px">
    <div class="stars"><svg viewBox="0 0 14 14"><path d="M7 1l1.8 3.9 4.2.4-3.2 2.8 1 4.1L7 10 3.2 12.2l1-4.1L1 5.3l4.2-.4z" fill="#f28a1e"/></svg><svg viewBox="0 0 14 14"><path d="M7 1l1.8 3.9 4.2.4-3.2 2.8 1 4.1L7 10 3.2 12.2l1-4.1L1 5.3l4.2-.4z" fill="#f28a1e"/></svg><svg viewBox="0 0 14 14"><path d="M7 1l1.8 3.9 4.2.4-3.2 2.8 1 4.1L7 10 3.2 12.2l1-4.1L1 5.3l4.2-.4z" fill="#f28a1e"/></svg><svg viewBox="0 0 14 14"><path d="M7 1l1.8 3.9 4.2.4-3.2 2.8 1 4.1L7 10 3.2 12.2l1-4.1L1 5.3l4.2-.4z" fill="#f28a1e"/></svg><svg viewBox="0 0 14 14"><path d="M7 1l1.8 3.9 4.2.4-3.2 2.8 1 4.1L7 10 3.2 12.2l1-4.1L1 5.3l4.2-.4z" fill="#f28a1e"/></svg></div>
    <span class="qmark">”</span>
    <p>"Working with Reach Crafters gave us the clarity and systems we needed to scale efficiently. Their intelligence reports alone have paid for the engagement 10x over."</p>
    <div class="author"><span class="avatar">H</span><div><b>Helena Marsh</b><small>CEO, Summit Advisory Group</small></div></div>
  </div>
  <div class="dots"><i></i><i></i><i></i><i></i><i></i><i></i></div>
</section>

<section class="blog">
  <h2 class="sec-title" style="top:64px">Latest <span class="hl">Blog</span> Posts</h2>
  <div class="sec-rule" style="top:124px"></div>

  <article class="post" style="left:140px">
    <div class="post-img" role="img" aria-label="Photo of a desk with a coffee cup, glasses and a notepad sketch about leads" style="background:linear-gradient(135deg,#7a4e2e,#c8a98a 55%,#e8e2d8)"><div class="date">28<small>JAN</small></div></div>
    <div class="post-body"><h3>How to 3x Your Lead Quality in 90 Days</h3><p>Proven tactics from top consultants that help you attract premium clients and eliminate time-wasters...</p><div class="more">Learn More <svg viewBox="0 0 14 10"><path d="M0 5h12M8 1l4 4-4 4" stroke="#2d5cf2" fill="none" stroke-width="1.3"/></svg></div></div>
  </article>
  <article class="post" style="left:458px">
    <div class="post-img" role="img" aria-label="Photo of a hand pointing at a rising blue bar chart" style="background:linear-gradient(135deg,#e9edf2,#cfd9e6 50%,#f4f6f8)"><div class="date">28<small>JAN</small></div></div>
    <div class="post-body"><h3>The Hidden Leaks Killing High-Ticket Sales</h3><p>Common mistakes and fixes for service businesses struggling to convert premium prospects into...</p><div class="more">Learn More <svg viewBox="0 0 14 10"><path d="M0 5h12M8 1l4 4-4 4" stroke="#2d5cf2" fill="none" stroke-width="1.3"/></svg></div></div>
  </article>
  <article class="post" style="left:776px">
    <div class="post-img" role="img" aria-label="Photo of three colleagues reviewing work in an office" style="background:linear-gradient(135deg,#6b6f78,#a9a7a2 50%,#d4d2cc)"><div class="date">28<small>JAN</small></div></div>
    <div class="post-body"><h3>Positioning for Premium Clients in 2026</h3><p>Be found. Be chosen. Learn the positioning strategies that make your firm the obvious choice for...</p><div class="more">Learn More <svg viewBox="0 0 14 10"><path d="M0 5h12M8 1l4 4-4 4" stroke="#2d5cf2" fill="none" stroke-width="1.3"/></svg></div></div>
  </article>

  <span class="btn" style="left:543px;top:537px;width:113px;height:40px">View All <svg viewBox="0 0 14 10"><path d="M0 5h12M8 1l4 4-4 4" stroke="#fff" fill="none" stroke-width="1.3"/></svg></span>
</section>

<section class="cta">
  <h2 class="abs cta-title">Ready to Become a <b>Reach Crafter?</b></h2>
  <p class="abs cta-text">Schedule a free strategy session and discover how our frameworks can<br>transform your sales and marketing funnel.</p>
  <span class="cta-btn">Schedule Your Strategy Call Now <svg viewBox="0 0 16 10"><path d="M0 5h14M10 1l4 4-4 4" stroke="#2d5cf2" fill="none" stroke-width="1.3"/></svg></span>
</section>

<footer class="site-footer">
  <div class="abs f-brand">Reach Crafters</div>
  <p class="abs f-about">Lorem ipsum dolor sit amet, consectetur adipiscing elit, sed do</p>
  <div class="abs follow">Follow Us: <i></i><i class="on"></i><i></i></div>

  <div class="abs f-col" style="left:449px;top:68px"><h4>Quick Links</h4><div class="rule"></div>
    <ul><li>About us</li><li>Services</li><li>Insights</li><li>Contact Us</li></ul></div>
  <div class="abs f-col" style="left:629px;top:68px"><h4>Services</h4><div class="rule" style="width:120px"></div>
    <ul><li>Executive Training</li><li>Funnel Optimization</li><li>Demand Generation</li></ul></div>
  <div class="abs f-col" style="left:842px;top:68px"><h4>Contact Details</h4><div class="rule" style="width:218px"></div>
    <div class="contact-row"><span class="c-ico"><svg viewBox="0 0 15 15"><path d="M7.5 1a4.5 4.5 0 0 0-4.5 4.5C3 9 7.5 14 7.5 14S12 9 12 5.5A4.5 4.5 0 0 0 7.5 1z" fill="none" stroke="#0e1a2f" stroke-width="1.3"/><circle cx="7.5" cy="5.5" r="1.6" fill="#0e1a2f"/></svg></span><span>123Lorem Ipsum, is simply<br>dummy text, of the printing.</span></div>
    <div class="contact-row" style="align-items:center"><span class="c-ico blue"><svg viewBox="0 0 15 15"><path d="M3 1.5l2.5 0 1 3-1.5 1a8 8 0 0 0 4.5 4.5l1-1.5 3 1v2.5a1 1 0 0 1-1 1A11 11 0 0 1 2 2.5a1 1 0 0 1 1-1z" fill="#fff"/></svg></span><span>Phone: (555) 014 2290</span></div>
    <div class="contact-row" style="align-items:center"><span class="c-ico" style="background:#2a3650"><svg viewBox="0 0 15 15"><rect x="1.5" y="3" width="12" height="9" rx="1" fill="none" stroke="#fff" stroke-width="1.2"/><path d="M1.5 3.5l6 4.5 6-4.5" fill="none" stroke="#fff" stroke-width="1.2"/></svg></span><span>hello@reachcrafters.example</span></div>
  </div>

  <div class="abs copy-rule"></div>
  <p class="abs copy">© 2023 Reach Crafters. All rights reserved. | Privacy Policy | Terms of Service</p>
</footer>

</body>
</html>
```